Real Estate investment company needs billboard designs

This is our website: https://brightlanepropertygroup.com/
We are looking for some billboard concepts that uses our CEO in the design. I have attached some images and 1 billboard design that someone in our industry uses, but we don't want it exactly like his.

Industry/Entity Type

real estate

Colors

Designer to choose colors to be used in the design.

Requirements
Must have
• Company colors from websiute

```html
<!DOCTYPE html>
<html lang="en">
<head>
<meta charset="utf-8">
<title>Bright Lane Property Group – Billboard</title>
<link href="https://fonts.googleapis.com/css2?family=Oswald:wght@600;700&family=Montserrat:wght@600;700;800&display=swap" rel="stylesheet">
<style>
  :root {
    --navy: #1b1a3f;
    --red: #ee1c25;
    --board: #ececee;
    --house-light: #e4e4e6;
    --house-mid: #c9c9cc;
    --shirt: #8a9cc4;
    --stage: #dfe3e8;
  }
  * { margin: 0; padding: 0; box-sizing: border-box; }
  html, body { width: 1200px; height: 1200px; overflow: hidden; }
  body {
    background: var(--stage);
    display: flex;
    align-items: center;
    justify-content: center;
  }
  .billboard {
    position: relative;
    width: 1140px;
    height: 560px;
    background: var(--board);
    overflow: hidden;
  }
  .house-photo {
    position: absolute;
    left: 0; top: 0;
    width: 100%; height: 100%;
    background: radial-gradient(ellipse at 48% 60%, var(--house-mid) 0%, var(--house-light) 45%, var(--board) 80%);
    opacity: 0.9;
  }
  .headline {
    position: absolute;
    left: 60px; top: 30px;
    width: 790px;
    font-family: "Oswald", sans-serif;
    font-weight: 700;
    color: var(--navy);
    line-height: 0.95;
    letter-spacing: -1px;
    white-space: nowrap;
  }
  .headline .line-main { display: block; font-size: 100px; }
  .headline .line-sub { display: block; font-size: 70px; margin-top: 6px; }
  .headline .accent { color: var(--red); }
  .brand {
    position: absolute;
    right: 30px; top: 140px;
    width: 220px;
    display: flex;
    align-items: center;
    gap: 10px;
    font-family: "Montserrat", sans-serif;
    font-weight: 800;
    font-size: 20px;
    line-height: 1.15;
    color: var(--navy);
  }
  .brand .mark {
    flex: none;
    width: 20px; height: 20px;
    background: var(--red);
  }
  .ceo-photo {
    position: absolute;
    right: 0; bottom: 0;
    width: 370px; height: 330px;
    background: linear-gradient(180deg, rgba(138,156,196,0.35) 0%, var(--shirt) 60%, #6f83b0 100%);
    border-radius: 160px 160px 0 0;
  }
  .contact {
    position: absolute;
    left: 56px; bottom: 50px;
    font-family: "Montserrat", sans-serif;
    color: var(--navy);
  }
  .phone {
    display: flex;
    align-items: center;
    gap: 14px;
    font-weight: 800;
    font-size: 84px;
    letter-spacing: -1px;
    line-height: 1;
  }
  .phone svg { width: 58px; height: 58px; flex: none; }
  .website {
    margin-top: 8px;
    font-weight: 700;
    font-size: 34px;
  }
  .website .domain { color: var(--red); }
</style>
</head>
<body>
  <main class="billboard">
    <div class="house-photo" role="img" aria-label="Soft grey photo of a two-storey suburban house with trees"></div>

    <h1 class="headline">
      <span class="line-main">Selling Your Home?</span>
      <span class="line-sub">Get a Cash Offer, <span class="accent">Same Day.</span></span>
    </h1>

    <div class="brand">
      <span class="mark"></span>
      <span class="brand-name">Bright Lane Property Group</span>
    </div>

    <div class="ceo-photo" role="img" aria-label="Company CEO in a light blue shirt, smiling and pointing up at the headline"></div>

    <div class="contact">
      <div class="phone">
        <svg viewBox="0 0 64 64" aria-hidden="true">
          <path d="M18 6c3 0 5 6 7 11 1 3-1 5-4 7 2 7 8 14 15 17 2-3 4-5 7-4 5 2 11 4 11 7 0 5-5 12-11 12C26 56 8 38 8 18 8 12 13 6 18 6z" fill="var(--red)"/>
          <path d="M40 10a16 16 0 0 1 14 14M40 18a8 8 0 0 1 6 6" stroke="var(--red)" stroke-width="4" fill="none" stroke-linecap="round"/>
        </svg>
        <span>555-014-2290</span>
      </div>
      <div class="website">www.<span class="domain">brightlanepropertygroup</span>.com</div>
    </div>
  </main>
</body>
</html>
```